BOLD & MINIMALIST DESIGN NEEDED

We want a very bold but minimalistic business card design that is impactful and utilizes both sides of the business card. Our current logo is included for your use.

We want bold fonts and good use of negative space. We don't want the logo to overpower the design.

Target Market(s)

Professionals who are building new commercial buildings.

Industry/Entity Type

Construction

Contact Information for Business Card

Name, Title, email, office phone, cell phone, website

Font styles to use
Serif
Sans Serif

Requirements
Must have
• Bold design!

```html
<!DOCTYPE html>
<html lang="en">
<head>
<meta charset="utf-8">
<title>Ridgecrest Design + Build — Business Card</title>
<link href="https://fonts.googleapis.com/css2?family=Montserrat:wght@400;500;800&display=swap" rel="stylesheet">
<style>
  :root {
    --backdrop: #3a3a3a;
    --card: #1c1c1c;
    --accent: #8cd13f;
    --ink: #ffffff;
    --muted: #d9d9d9;
  }
  * { box-sizing: border-box; margin: 0; padding: 0; }
  html, body { width: 1200px; height: 791px; overflow: hidden; }
  body {
    background: var(--backdrop);
    font-family: "Montserrat", sans-serif;
    color: var(--ink);
    display: flex;
    align-items: center;
    justify-content: center;
    gap: 60px;
  }
  .card {
    width: 520px;
    height: 297px;
    background: var(--card);
    border-bottom: 3px solid var(--accent);
    border-right: 3px solid var(--accent);
    position: relative;
  }
  .brand {
    display: flex;
    align-items: center;
    gap: 10px;
    font-weight: 800;
    color: var(--ink);
    text-transform: uppercase;
    letter-spacing: 0.01em;
    line-height: 1.1;
  }
  .brand-square { background: var(--accent); flex: none; }

  /* Back side: contact details */
  .card-back .brand {
    position: absolute;
    left: 40px;
    top: 78px;
    font-size: 20px;
  }
  .card-back .brand-square { width: 14px; height: 14px; }
  .divider {
    position: absolute;
    left: 268px;
    top: 70px;
    width: 2px;
    height: 76px;
    background: var(--accent);
  }
  .contact-list {
    position: absolute;
    left: 292px;
    top: 66px;
    list-style: none;
    font-size: 13px;
    font-weight: 500;
    color: var(--muted);
  }
  .contact-list li {
    display: flex;
    align-items: center;
    gap: 9px;
    height: 21px;
  }
  .contact-list svg { width: 11px; height: 11px; flex: none; }
  .person {
    position: absolute;
    left: 40px;
    bottom: 44px;
  }
  .person-name {
    font-size: 21px;
    font-weight: 800;
    color: var(--accent);
    text-transform: uppercase;
  }
  .person-title {
    font-size: 14px;
    font-weight: 400;
    color: var(--ink);
    margin-top: 2px;
  }

  /* Front side: brand */
  .card-front {
    display: flex;
    align-items: center;
    justify-content: center;
    padding: 0 48px;
  }
  .card-front .brand { font-size: 32px; gap: 16px; }
  .card-front .brand-square { width: 26px; height: 26px; }
</style>
</head>
<body>
  <section class="card card-back" aria-label="Card back">
    <div class="brand"><span class="brand-square"></span><span>Ridgecrest<br>Design + Build</span></div>
    <div class="divider"></div>
    <ul class="contact-list">
      <li>
        <svg viewBox="0 0 12 12" aria-hidden="true"><path fill="#8cd13f" d="M2.5 1l2 2.2-1 1.3a6 6 0 0 0 4 4l1.3-1 2.2 2-1.3 1.5C5 11 1 7 1 2.3z"/></svg>
        555-014-2200
      </li>
      <li>
        <svg viewBox="0 0 12 12" aria-hidden="true"><rect x="3" y="0.8" width="6" height="10.4" rx="1" fill="none" stroke="#8cd13f" stroke-width="1.3"/></svg>
        555-014-2201
      </li>
      <li>
        <svg viewBox="0 0 12 12" aria-hidden="true"><rect x="0.8" y="2.5" width="10.4" height="7" fill="#8cd13f"/><path d="M1 3l5 3.5L11 3" fill="none" stroke="#1c1c1c" stroke-width="1"/></svg>
        m.avery@rdb-build.com
      </li>
      <li>
        <svg viewBox="0 0 12 12" aria-hidden="true"><circle cx="6" cy="6" r="5" fill="none" stroke="#8cd13f" stroke-width="1.3"/><path d="M1 6h10M6 1c-2.5 3-2.5 7 0 10M6 1c2.5 3 2.5 7 0 10" fill="none" stroke="#8cd13f" stroke-width="0.9"/></svg>
        www.rdb-build.com
      </li>
    </ul>
    <div class="person">
      <p class="person-name">Marcus Avery</p>
      <p class="person-title">President</p>
    </div>
  </section>

  <section class="card card-front" aria-label="Card front">
    <div class="brand"><span class="brand-square"></span><span>Ridgecrest<br>Design + Build</span></div>
  </section>
</body>
</html>
```